Tablet App design for business management system

TaskOra is a business management system made especially for service based businesses (our subscribers). It enables systemising your service businesses. This can be used by diverse industries like automotive service, beauty (hair salons, nail spas), Spas, Chiropractor, acupuntcure, osteo, yoga studio, business coach, etc.

The UI of the app needs to be designed using flat and clean UI design trends that are currently prevailing for B2C apps. Even the sliding menu panel can be removed and alternative placement of this functionality can be suggested. The color palette used for the design should be limited (3-5 colours)

The Current UI screens are open to suggestions for change. For ease of management in minimum steps, consolidation of functionality on different screens can be suggested, accompanies by a rational reason with the objective of having a simple and straight forward user experience.

User should be able to move from one function to another (booking > view appointments > profile) in no more than 1 or max 2 gestures.

Target Market(s)

SME businesses that provide time based services

Industry/Entity Type

Business

Font styles to use
Sans Serif

Requirements
Must have
• The power point slides give a detailed account of the process flow and functionality that the app is to follow.
• Reference this slide to ensure that your final design must have all screens that are required to deliver the functionality.

```html
<!DOCTYPE html>
<html lang="en">
<head>
<meta charset="utf-8">
<title>TaskOra – Sign In</title>
<link href="https://fonts.googleapis.com/css2?family=Roboto:wght@400;500&family=Great+Vibes&display=swap" rel="stylesheet">
<style>
  :root {
    --ink-light: #ffffff;
    --ink-soft: rgba(255,255,255,0.85);
    --script-brown: #b8701a;
    --action-green: #6db30f;
    --rule: rgba(255,255,255,0.75);
  }
  * { box-sizing: border-box; margin: 0; padding: 0; }
  html, body { width: 1200px; height: 900px; overflow: hidden; }
  body { font-family: 'Roboto', sans-serif; color: var(--ink-light); }

  .screen { position: relative; width: 1200px; height: 900px; overflow: hidden; }

  .backdrop {
    position: absolute; inset: 0;
    background:
      radial-gradient(ellipse 260px 420px at 0% 100%, rgba(110,60,100,0.85), transparent 70%),
      radial-gradient(ellipse 200px 200px at 130px 520px, rgba(150,80,100,0.6), transparent 70%),
      radial-gradient(ellipse 500px 380px at 380px 650px, rgba(215,105,95,0.85), transparent 70%),
      radial-gradient(ellipse 420px 300px at 700px 800px, rgba(220,120,95,0.7), transparent 70%),
      radial-gradient(ellipse 420px 420px at 1150px 650px, rgba(225,215,115,0.9), transparent 70%),
      radial-gradient(ellipse 300px 200px at 1100px 300px, rgba(230,220,190,0.8), transparent 70%),
      radial-gradient(ellipse 400px 180px at 560px 480px, rgba(185,115,100,0.45), transparent 70%),
      radial-gradient(ellipse 340px 160px at 360px 220px, rgba(190,160,120,0.4), transparent 70%),
      linear-gradient(180deg, #c9d2ac 0%, #dcc99a 25%, #e2b583 42%, #dc9478 60%, #d98a72 100%);
  }

  .status-bar {
    position: absolute; top: 0; left: 0; right: 0; height: 38px;
    display: flex; align-items: center; justify-content: space-between;
    padding: 0 18px; font-size: 17px; color: var(--ink-light);
  }
  .status-bar .device { display: flex; align-items: center; gap: 8px; }
  .status-bar .time { position: absolute; left: 0; right: 0; text-align: center; pointer-events: none; }
  .status-bar .battery { display: flex; align-items: center; gap: 8px; }

  .welcome {
    position: absolute; top: 140px; left: 0; right: 0; text-align: center;
    font-family: 'Great Vibes', cursive; font-size: 96px; color: var(--script-brown);
    line-height: 1;
  }

  .login-form { position: absolute; left: 272px; top: 340px; width: 655px; }

  .field {
    position: relative; height: 70px; display: flex; align-items: center;
    border-bottom: 1px solid var(--rule); margin-bottom: 16px;
  }
  .field::before, .field::after {
    content: ""; position: absolute; bottom: 0; width: 1px; height: 7px; background: var(--rule);
  }
  .field::before { left: 0; }
  .field::after { right: 0; }
  .field-icon { width: 34px; margin-left: 22px; display: flex; justify-content: center; }
  .field-label { margin-left: 25px; font-size: 18px; color: var(--ink-light); }

  .login-button {
    position: absolute; left: 272px; top: 577px; width: 655px; height: 68px;
    background: var(--action-green); border: 0; color: var(--ink-light);
    display: flex; align-items: center; justify-content: center; gap: 16px;
    font-family: 'Roboto', sans-serif; font-weight: 500; font-size: 22px;
  }

  .account-links {
    position: absolute; top: 656px; left: 0; right: 0; height: 24px; font-size: 16px;
  }
  .account-links a { position: absolute; color: var(--ink-soft); text-decoration: underline; transform: translateX(-50%); }
  .account-links .forgot { left: 490px; }
  .account-links .signup { left: 705px; top: 2px; }
  .account-links .divider { position: absolute; left: 600px; top: 2px; width: 1px; height: 22px; background: rgba(80,60,60,0.6); }
</style>
</head>
<body>
<main class="screen">
  <div class="backdrop" role="img" aria-label="Softly blurred warm photograph in cream, coral and yellow tones"></div>

  <header class="status-bar">
    <span class="device">Tablet
      <svg width="18" height="14" viewBox="0 0 18 14" fill="#fff"><path d="M9 13l2.5-3a4 4 0 0 0-5 0z"/><path d="M9 6.5a7 7 0 0 1 4.6 1.7l1.4-1.7A9.2 9.2 0 0 0 9 4.3 9.2 9.2 0 0 0 3 6.5l1.4 1.7A7 7 0 0 1 9 6.5z"/><path d="M9 2.2a11.4 11.4 0 0 1 7.4 2.7L17.8 3.2A13.6 13.6 0 0 0 9 0 13.6 13.6 0 0 0 .2 3.2l1.4 1.7A11.4 11.4 0 0 1 9 2.2z"/></svg>
    </span>
    <span class="time">4:21 PM</span>
    <span class="battery">
      <svg width="10" height="16" viewBox="0 0 10 16" fill="none" stroke="rgba(255,255,255,0.7)" stroke-width="1.2"><path d="M1 4l8 8-4 3V1l4 3-8 8"/></svg>
      100%
      <svg width="40" height="16" viewBox="0 0 40 16"><rect x="0.5" y="0.5" width="35" height="15" rx="3" fill="none" stroke="#fff"/><rect x="2.5" y="2.5" width="31" height="11" rx="1.5" fill="#fff"/><rect x="37" y="5" width="2" height="6" rx="1" fill="#fff"/></svg>
    </span>
  </header>

  <h1 class="welcome">Welcome</h1>

  <form class="login-form">
    <div class="field">
      <span class="field-icon">
        <svg width="32" height="32" viewBox="0 0 32 32" fill="none" stroke="#fff" stroke-width="1.6"><circle cx="16" cy="11" r="7"/><path d="M2 31c1-8 7-11 14-11s13 3 14 11z"/></svg>
      </span>
      <span class="field-label">User Name</span>
    </div>
    <div class="field">
      <span class="field-icon">
        <svg width="26" height="34" viewBox="0 0 26 34" fill="none" stroke="#fff" stroke-width="1.6"><path d="M5 15V10a8 8 0 0 1 16 0v5"/><rect x="1" y="15" width="24" height="18" rx="3"/></svg>
      </span>
      <span class="field-label">Password</span>
    </div>
  </form>

  <button class="login-button" type="button">
    <svg width="24" height="22" viewBox="0 0 24 22" fill="none" stroke="#fff" stroke-width="1.5"><path d="M6 6V1h17v20H6v-5"/><path d="M1 11h13M10 7l4 4-4 4"/></svg>
    LOG IN
  </button>

  <nav class="account-links">
    <a class="forgot" href="#">Forgot Password?</a>
    <span class="divider"></span>
    <a class="signup" href="#">Need Accound</a>
  </nav>
</main>
</body>
</html>
```